Web design for Crowdfunding site HopeWingsRally.com

We need a web design for christian crowdfunding website. Here is the challenge: We need responsive layout that is targeted first in iPad size of screen. It should also scale somehow down to iPhone size of screens. Web layout can be about the same size as iPad screen.

Screens should work so that main page scrolls not but only certain part of the screen scrolls and always one "page" at time. We can implement these "scrolls" then later with javascript but now we need only design. The challenge is to create this kind of hybrid website / app look.

Target is at first to raise funds to orphan people needing about $40 per month for their living and education. There is always some organization which takes care of these kids. Later there will be other christian missions included. At first we are looking to find monthly supporters.

You can be as creative as you want :) As you see from the look and feel sector, I am not looking any same traditional look which many "help kids" sites have. I am looking to reach now younger generation and therefore iPad and mobile are the main screen sizes.

Inspirational designs:
- https://example-gallery.test/profiles/studiofernlake/designs/482716?from=%2Fbrowse%2Fxhr%2Fdesigns%3Fcategory%3Dmobile-app-design
- http://www.artpoolhub.test/design/8261047 Clear, simple visuals
- http://www.artpoolhub.test/design/7394215 Header
- http://www.artpoolhub.test/design/6048392 Contrast in the colors, i think is powerfull

Some terms could be: Kids play, kids are learning (in the school). No static posture but living like kids are. I wonder also how we could also add little bit gaming style even though the question is of reali life of real people. Giving should be rewarding.

Target Market(s)

People who want help other people.

Industry/Entity Type

Christian

Number of Pages Required

4 page

Requirements
Must have
• Homepage. Mission page (In my wireframes it was one kid).
Nice to have
• Other pages and some idea how to scroll. 4 pages is no must. If you feel easy, please give first some draft and I give comments on that.

```html
<!DOCTYPE html>
<html lang="en">
<head>
<meta charset="utf-8">
<title>HopeWingsRally</title>
<link rel="stylesheet" href="https://fonts.googleapis.com/css2?family=Roboto:wght@300;400;500;700&display=swap">
<style>
  :root {
    --brand-yellow: #ffb400;
    --brand-yellow-dark: #d99a00;
    --bar-dark: #2a2a2a;
    --white: #ffffff;
    --footer-text: #c9c9c9;
    --social-grey: #5e5e5e;
    --social-ring: #6c6c6c;
    --dot: rgba(255,255,255,0.45);
    --sky-navy: #1c2436;
    --sky-deep: #2f3d55;
    --sky-mid: #6d819c;
    --sky-light: #c9d7e4;
    --sky-warm: #a59d8c;
    --hill: #0f1524;
  }
  * { margin: 0; padding: 0; box-sizing: border-box; }
  html, body { width: 1200px; height: 629px; overflow: hidden; background: var(--bar-dark); }
  body { font-family: "Roboto", Arial, sans-serif; color: var(--white); position: relative; }

  .site-header {
    position: absolute; top: 0; left: 0; width: 1200px; height: 69px;
    background: var(--bar-dark);
  }
  .menu-toggle {
    position: absolute; left: 0; top: 0; width: 68px; height: 69px;
    background: var(--brand-yellow);
    display: flex; align-items: center; justify-content: center;
  }
  .nav-link {
    position: absolute; left: 91px; top: 29px;
    font-size: 12px; font-weight: 500; color: var(--white);
  }
  .search-icon { position: absolute; left: 221px; top: 28px; }
  .brand-name {
    position: absolute; left: 0; width: 1200px; top: 17px; text-align: center;
    font-size: 28px; font-weight: 700; color: var(--brand-yellow);
    letter-spacing: -0.3px;
  }
  .social-list { position: absolute; left: 862px; top: 20px; display: flex; gap: 6px; }
  .social-dot {
    width: 28px; height: 28px; border-radius: 50%;
    background: var(--social-grey);
    box-shadow: inset 0 0 0 1px var(--social-ring);
  }
  .auth-btn {
    position: absolute; top: 20px; width: 85px; height: 33px;
    background: var(--brand-yellow);
    border-bottom: 2px solid var(--brand-yellow-dark);
    border-radius: 2px;
    font-size: 12px; font-weight: 500; color: var(--white);
    display: flex; align-items: center; justify-content: center;
  }
  .auth-login { left: 983px; }
  .auth-signup { left: 1077px; }

  .hero { position: absolute; top: 69px; left: 0; width: 1200px; height: 506px; overflow: hidden; }
  .hero-backdrop {
    position: absolute; inset: 0;
    background:
      radial-gradient(ellipse 260px 60px at 850px 485px, var(--hill) 0%, rgba(15,21,36,0) 100%),
      radial-gradient(ellipse 180px 130px at 790px 200px, rgba(20,28,45,0.55) 0%, rgba(20,28,45,0) 100%),
      radial-gradient(ellipse 140px 110px at 1130px 340px, rgba(35,42,55,0.7) 0%, rgba(35,42,55,0) 100%),
      radial-gradient(ellipse 320px 200px at 900px 230px, var(--sky-light) 0%, rgba(201,215,228,0) 100%),
      radial-gradient(ellipse 200px 90px at 560px 420px, rgba(165,157,140,0.55) 0%, rgba(165,157,140,0) 100%),
      radial-gradient(ellipse 380px 260px at 150px 130px, var(--sky-navy) 0%, rgba(28,36,54,0) 100%),
      radial-gradient(ellipse 360px 140px at 200px 470px, rgba(40,50,68,0.8) 0%, rgba(40,50,68,0) 100%),
      linear-gradient(180deg, #55657c 0%, var(--sky-mid) 45%, #4a5a72 100%);
  }
  .hero-copy { position: absolute; left: 102px; top: 176px; width: 520px; }
  .hero-title { font-size: 37px; font-weight: 700; color: var(--brand-yellow); letter-spacing: -0.3px; line-height: 1.2; }
  .hero-text { font-size: 21px; font-weight: 300; line-height: 33px; margin-top: 6px; }
  .hero-text + .hero-text { margin-top: 6px; }

  .page-dots { position: absolute; left: 1156px; top: 199px; display: flex; flex-direction: column; gap: 17px; }
  .page-dot { width: 8px; height: 8px; border-radius: 50%; background: var(--dot); }

  .site-footer {
    position: absolute; top: 575px; left: 0; width: 1200px; height: 54px;
    background: var(--bar-dark);
    display: flex; align-items: center; justify-content: center;
    font-size: 12px; color: var(--footer-text);
  }
</style>
</head>
<body>
  <header class="site-header">
    <div class="menu-toggle">
      <svg width="26" height="20" viewBox="0 0 26 20" aria-hidden="true">
        <rect x="0" y="1" width="26" height="2" fill="#fff"/>
        <rect x="0" y="9" width="26" height="2" fill="#fff"/>
        <rect x="0" y="17" width="26" height="2" fill="#fff"/>
      </svg>
    </div>
    <span class="nav-link">SEE THE MISSIONS</span>
    <svg class="search-icon" width="13" height="13" viewBox="0 0 13 13" aria-label="Search">
      <circle cx="5.3" cy="5.3" r="4.1" fill="none" stroke="#fff" stroke-width="1.8"/>
      <line x1="8.3" y1="8.3" x2="12" y2="12" stroke="#fff" stroke-width="2" stroke-linecap="round"/>
    </svg>
    <div class="brand-name">HOPEWINGSRALLY</div>
    <div class="social-list" aria-label="Social links">
      <span class="social-dot"></span>
      <span class="social-dot"></span>
      <span class="social-dot"></span>
    </div>
    <span class="auth-btn auth-login">LOGIN</span>
    <span class="auth-btn auth-signup">SIGNUP</span>
  </header>

  <main class="hero">
    <div class="hero-backdrop" role="img" aria-label="Photo of three cross silhouettes on a hill against a dramatic cloudy sky"></div>
    <div class="hero-copy">
      <h1 class="hero-title">HOPEWINGSRALLY</h1>
      <p class="hero-text">She has a name. He hasdreams. She hopes she Would have a future. He is like You.</p>
      <p class="hero-text">I USD a month will help her and him.</p>
    </div>
    <nav class="page-dots" aria-label="Page sections">
      <span class="page-dot"></span>
      <span class="page-dot"></span>
      <span class="page-dot"></span>
      <span class="page-dot"></span>
      <span class="page-dot"></span>
    </nav>
  </main>

  <footer class="site-footer">Copyrights. 2016. HopeWingsRally. All rights reserved.</footer>
</body>
</html>
```